Business card design needed

I run a Beautician studio (for 7 years now)
I offer
- Velmo Body Sugaring
- Ruby Glaze
- Nails
- Facials
- Manicure
- Foot Treatment
It might not be necessary to list all those treatments?
Maybe the link to the Website is sufficient?
I leave that up to you ...
(more info on www.FernAndDewByLenka.com.au)
Velmo BodySugaring is our biggest success, It replaces waxing.
I would like to incorporate the logo into the Business Card.
We had many complaints regarding our old Business Cards as the Phone Number was to small.
On the backside, we would like a "your next Appointment" section.
Looking forward to you Design, cheers ... Lenka
Industry/Entity Type
Business
Contact Information for Business Card
Fern by Dew by Lenka
14 Korrin Sqr 3942 Alderlea
www.FernAndDewByLenka.com.au
03 9481 2267

```html
<!DOCTYPE html>
<html lang="en">
<head>
<meta charset="utf-8">
<title>Fern by Dew by Lenka – Business Card</title>
<link rel="stylesheet" href="https://fonts.googleapis.com/css2?family=Tinos:wght@400;700&family=Open+Sans:wght@400;600;700&family=Arimo:wght@400&display=swap">
<style>
  :root{
    --backdrop:#1c1c1c;
    --card:#ffffff;
    --ink:#3d3d3d;
    --ink-soft:#555555;
    --green:#2e9a3c;
    --orange:#e8542b;
    --amber:#f0952a;
    --yellow:#f5cc2c;
    --line:#9a9a9a;
    --faint:#efebe7;
  }
  *{box-sizing:border-box;margin:0;padding:0}
  html,body{width:1200px;height:720px;overflow:hidden;background:var(--backdrop)}
  body{position:relative;font-family:"Open Sans",Arial,sans-serif;color:var(--ink)}
  .card{position:absolute;background:var(--card);border-radius:18px;overflow:hidden}

  /* Front */
  .front{left:310px;top:31px;width:524px;height:299px;text-align:center}
  .front .brand-watermark{position:absolute;left:0;right:0;top:168px;font-size:50px;letter-spacing:10px;line-height:56px;color:var(--faint);font-weight:400}
  .business-name{position:absolute;left:0;right:0;top:20px;font-family:"Tinos",Georgia,serif;font-weight:700;font-size:31px;line-height:38px;color:var(--ink)}
  .tagline{position:absolute;left:0;right:0;top:58px;font-family:"Tinos",Georgia,serif;font-weight:400;font-size:16px;color:var(--ink)}
  .contact{position:absolute;left:0;right:0;display:flex;justify-content:center;align-items:center;gap:7px;font-family:"Arimo",Arial,sans-serif;color:#222}
  .contact.phone{top:112px;font-size:22px}
  .contact.web{top:151px;font-size:14px}
  .contact.address{top:207px;font-size:17px;letter-spacing:2.2px}
  .treatments{position:absolute;left:0;right:0;bottom:0;height:47px;background:linear-gradient(90deg,var(--orange),var(--amber) 50%,var(--yellow));color:#fff}
  .treatments h2{font-size:15px;font-weight:700;letter-spacing:.8px;margin-top:4px}
  .treatments ul{list-style:none;display:flex;justify-content:center;gap:8px;font-size:12.5px;margin-top:1px}
  .treatments li::before{content:"• "}

  /* Backs */
  .hours-title{color:var(--green);font-size:20px;letter-spacing:1.2px;font-weight:400}
  .hours{font-size:14.5px;font-weight:600;color:var(--ink-soft);line-height:21px}
  .brand{display:flex;flex-direction:column;align-items:center;gap:8px;color:var(--ink)}
  .brand .dot{width:46px;height:46px;border-radius:50%;background:var(--amber)}
  .brand .name{font-size:20px;letter-spacing:4px;font-weight:400;white-space:nowrap}

  .back-a{left:58px;top:367px;width:523px;height:298px}
  .back-a .hours-title{position:absolute;left:30px;top:9px}
  .back-a .hours{position:absolute;left:30px;top:38px}
  .back-a .brand{position:absolute;left:345px;top:22px}
  .appt-title{position:absolute;left:34px;top:94px;font-family:"Tinos",Georgia,serif;font-weight:400;color:var(--green);font-size:19px;letter-spacing:.3px}
  .field{position:absolute;left:34px;font-size:14.5px;color:var(--ink-soft);display:flex;align-items:center;gap:8px}
  .rule{display:inline-block;border-bottom:1px solid var(--line)}
  .rule.dotted{border-bottom-style:dotted}
  .box{display:inline-block;border:1px solid #777;border-radius:2px}
  .days{position:absolute;left:30px;top:244px;display:flex;align-items:center;gap:6px;font-size:14.5px;font-weight:600;color:var(--ink-soft)}
  .days .box{width:33px;height:20px;margin-right:2px}
  .notice{position:absolute;left:0;right:0;bottom:7px;text-align:center;font-size:10.5px;color:var(--ink)}

  .back-b{left:611px;top:367px;width:523px;height:299px}
  .back-b .hours-title{position:absolute;left:34px;top:58px}
  .back-b .hours{position:absolute;left:34px;top:87px}
  .back-b .brand{position:absolute;left:46px;top:148px}
  .divider{position:absolute;left:257px;top:38px;height:226px;border-left:1px solid #bbb}
  .back-b .side{position:absolute;left:276px;top:44px;width:230px;font-size:14.5px;color:var(--ink-soft)}
  .side .rule{width:218px;display:block}
  .side .has{font-weight:600;margin-top:8px}
  .day-grid{display:flex;gap:12px;margin-top:22px;font-weight:600;font-size:13.5px}
  .day-grid span{display:flex;flex-direction:column;align-items:center;gap:5px}
  .day-grid .box{width:17px;height:11px}
  .side .line-field .rule{display:inline-block;border-color:#555}
  .side .advance{margin-top:22px;line-height:21px}
</style>
</head>
<body>

<section class="card front">
  <div class="brand-watermark" aria-hidden="true">VELMO</div>
  <h1 class="business-name">Fern by Dew by Lenka</h1>
  <p class="tagline">In the heart of Wendaree</p>
  <p class="contact phone">
    <svg width="20" height="20" viewBox="0 0 20 20" aria-hidden="true"><circle cx="10" cy="10" r="9" fill="var(--amber)"/><path d="M7 5.5c-1 1-1 3 .8 5.5s4 3.6 5 3l1-1-1.8-1.6-1 .7c-.8-.3-2.4-2-2.6-2.8l.8-.9L7.9 5z" fill="#fff"/></svg>
    03 9481 2267
  </p>
  <p class="contact web">
    <svg width="14" height="14" viewBox="0 0 14 14" aria-hidden="true"><circle cx="7" cy="7" r="6" fill="none" stroke="var(--amber)" stroke-width="1.4"/><path d="M1 7h12M7 1c-3 3-3 9 0 12M7 1c3 3 3 9 0 12" fill="none" stroke="var(--amber)" stroke-width="1"/></svg>
    www.FernAndDewByLenka.com.au
  </p>
  <p class="contact address">
    <svg width="13" height="15" viewBox="0 0 13 15" aria-hidden="true"><path d="M6.5 0a6 6 0 0 1 6 6c0 4-6 9-6 9s-6-5-6-9a6 6 0 0 1 6-6z" fill="#333"/><circle cx="6.5" cy="6" r="2.2" fill="#fff"/></svg>
    14 Korrin Sqr 3942 Alderlea
  </p>
  <div class="treatments">
    <h2>Treatments offered</h2>
    <ul>
      <li>Velmo Body Sugaring</li><li>Ruby Glaze</li><li>Nails</li><li>Facials</li><li>Manicure</li><li>Foot Treatment</li>
    </ul>
  </div>
</section>

<section class="card back-a">
  <h2 class="hours-title">Hours of Operation</h2>
  <p class="hours">Mon - Fri:&nbsp; 7.30am - 7.00pm<br>Saturday: 7.30am - 12.00pm</p>
  <div class="brand"><span class="dot"></span><span class="name">VELMO</span></div>
  <h3 class="appt-title">YOUR APPOINTMENT</h3>
  <p class="field" style="top:132px">Name : <span class="rule dotted" style="width:290px;margin-left:6px"></span></p>
  <p class="field" style="top:170px">Date : <span class="rule" style="width:95px;margin-left:12px"></span> Time : <span class="rule" style="width:88px"></span> am / pm</p>
  <p class="field" style="top:206px">Next Appointment <span class="box" style="width:95px;height:21px;margin-left:4px"></span><span class="box" style="width:95px;height:21px;margin-left:26px"></span></p>
  <div class="days">MON <span class="box"></span>TUE <span class="box"></span>WED <span class="box"></span>THU <span class="box"></span>FRI <span class="box"></span>SAT <span class="box"></span></div>
  <p class="notice">It would be appreciated if 24 hours notice could be given if you are unable to attend an appointment</p>
</section>

<section class="card back-b">
  <h2 class="hours-title">Hours of Operation</h2>
  <p class="hours">Mon - Fri:&nbsp; 7.30am - 7.00pm<br>Saturday: 7.30am - 12.00pm</p>
  <div class="brand"><span class="dot"></span><span class="name">VELMO</span></div>
  <div class="divider"></div>
  <div class="side">
    <span class="rule dotted"></span>
    <p class="has">has an appointment</p>
    <div class="day-grid">
      <span>MON<i class="box"></i></span><span>TUE<i class="box"></i></span><span>WED<i class="box"></i></span><span>THU<i class="box"></i></span><span>FRI<i class="box"></i></span><span>SAT<i class="box"></i></span>
    </div>
    <p class="line-field" style="margin-top:18px">Date : <span class="rule" style="width:148px"></span></p>
    <p class="line-field" style="margin-top:12px">Time : <span class="rule" style="width:120px"></span> AM/PM</p>
    <p class="advance">Advance notice requested for appointment cancellation</p>
  </div>
</section>

</body>
</html>
```